We are a recruitment company based in Fenbridge/Cambridge England.
I have included our company logo which we want to remain the same.

What we are looking for is a new creative Business card which will really stand out!!

Contact Information for Business Card

Harriet Dunmore
email: Harriet@plavex.co.uk
Address: Brackwell House
Fenmoor Enterprise Park
Partridge Way
Fenbridge
QB9 3KX
Tel:01632 960418

```html
<!DOCTYPE html>
<html lang="en">
<head>
<meta charset="utf-8">
<title>Plavex – Business Card</title>
<link rel="stylesheet" href="https://fonts.googleapis.com/css2?family=Jost:wght@400;500;600&family=Quicksand:wght@500;700&display=swap">
<style>
  :root {
    --backdrop: #2e2e2e;
    --brand-green: #86c440;
    --brand-green-light: #93cc52;
    --ink-grey: #6d6e71;
    --ink-dark: #231f20;
    --rule-grey: #8a8a8a;
    --paper: #ffffff;
  }
  * { box-sizing: border-box; margin: 0; padding: 0; }
  html, body {
    width: 1200px; height: 800px; overflow: hidden;
    background: var(--backdrop);
  }
  .canvas { position: relative; width: 1200px; height: 800px; }

  .card {
    position: absolute;
    width: 600px; height: 343px;
    box-shadow: 0 10px 30px rgba(0,0,0,.45);
    overflow: hidden;
  }

  /* Front */
  .card--front { left: 60px; top: 50px; background: var(--brand-green); }
  .front__texture {
    position: absolute; inset: 0;
    background: radial-gradient(ellipse at 50% 45%, var(--brand-green-light) 0%, var(--brand-green) 70%);
  }
  .brand {
    position: absolute; display: flex; align-items: center; gap: 14px;
  }
  .brand__dot { border-radius: 50%; flex: none; }
  .brand__name {
    font-family: "Quicksand", sans-serif; font-weight: 700; line-height: 1;
  }
  .brand__tagline {
    font-family: "Quicksand", sans-serif; font-weight: 500;
    text-transform: capitalize; letter-spacing: .28em; line-height: 1;
  }
  .card--front .brand { left: 50%; top: 128px; transform: translateX(-50%); }
  .card--front .brand__dot { width: 62px; height: 62px; background: var(--paper); }
  .card--front .brand__name { font-size: 46px; color: var(--paper); }
  .card--front .brand__tagline { font-size: 8px; color: var(--paper); margin-top: 5px; }
  .front__web {
    position: absolute; left: 0; right: 0; bottom: 36px; text-align: center;
    font-family: "Quicksand", sans-serif; font-size: 12px; font-weight: 500;
    letter-spacing: .2em; color: var(--paper);
  }

  /* Back */
  .card--back { left: 560px; top: 410px; background: var(--paper); }
  .card--back .brand { right: 36px; top: 38px; }
  .card--back .brand__dot { width: 52px; height: 52px; background: var(--ink-grey); }
  .card--back .brand__name { font-size: 38px; color: var(--brand-green); }
  .card--back .brand__tagline { font-size: 7px; color: var(--ink-grey); margin-top: 4px; }
  .back__top-rule {
    position: absolute; left: 210px; right: 36px; top: 124px;
    height: 1px; background: var(--rule-grey);
  }
  .holder {
    position: absolute; left: 0; top: 178px; padding-left: 44px;
    font-family: "Jost", sans-serif;
  }
  .holder::before {
    content: ""; position: absolute; left: 0; top: 4px;
    width: 9px; height: 44px; background: var(--brand-green);
  }
  .holder__name {
    font-size: 30px; font-weight: 600; color: var(--brand-green);
    letter-spacing: .03em; line-height: 1; text-transform: uppercase;
  }
  .holder__role {
    font-size: 16px; font-weight: 400; color: var(--ink-grey);
    letter-spacing: .02em; margin-top: 4px; text-transform: uppercase;
  }
  .back__mid-rule {
    position: absolute; left: 44px; right: 36px; top: 240px;
    height: 1px; background: var(--rule-grey);
  }
  .contact {
    position: absolute; left: 44px; right: 20px; top: 252px;
    font-family: "Jost", sans-serif; font-size: 13px; color: var(--ink-dark);
    line-height: 1.75; list-style: none;
  }
  .contact__sep { margin: 0 8px; }
  .back__band {
    position: absolute; left: 0; right: 0; bottom: 0; height: 10px;
    background: var(--brand-green);
  }
</style>
</head>
<body>
<main class="canvas">

  <section class="card card--front" aria-label="Business card front">
    <div class="front__texture" role="img" aria-label="Faint world map pattern on green"></div>
    <div class="brand">
      <span class="brand__dot"></span>
      <div>
        <div class="brand__name">Plavex</div>
        <div class="brand__tagline">Technology Recruitment</div>
      </div>
    </div>
    <p class="front__web">www.plavex.co.uk</p>
  </section>

  <section class="card card--back" aria-label="Business card back">
    <div class="brand">
      <span class="brand__dot"></span>
      <div>
        <div class="brand__name">Plavex</div>
        <div class="brand__tagline">Technology Recruitment</div>
      </div>
    </div>
    <div class="back__top-rule"></div>

    <div class="holder">
      <h1 class="holder__name">Harriet Dunmore</h1>
      <p class="holder__role">CEO &amp; Founder</p>
    </div>
    <div class="back__mid-rule"></div>

    <ul class="contact">
      <li>Tel : 01632 960418<span class="contact__sep">|</span>Email : Harriet@plavex.co.uk<span class="contact__sep">|</span>Web : www.plavex.co.uk</li>
      <li>Address : Brackwell House Fenmoor Enterprise Park, Partridge Way Fenbridge, QB9 3KX</li>
    </ul>
    <div class="back__band"></div>
  </section>

</main>
</body>
</html>
```